TL - business card

Tallow Partners is an insurance brokerage firm, inovative, proactive, vigorous, which aims to become the leader of the insurance brokers in Anfrica. We should like to get some designs which should be avoided also in Gray / Metallic for the Administration and Orange / Blue for the Managers (ike in the picture sent). The Blue / Green logo is not the correct one, but the source of the file. Please adjust the color accordingly for the business cards. 1 / Orange / Blue 2 / Gray / Metallic We want something classic but which is transmitted strenght, inovation, modernity and most of all, rapidity. We want something start-up like, very punchy and catching eye remaining profesional at the same time. Name: Dorian Whitlock Function: Managing Director Address: N ° 17/18 Rua Veloso - R / C 2B Direita - Bairro Mutamba - Luanda Tel: (+244) 947 582 316 Email: dorian.whitlock@tallow-p.example Website: www.tallow-p. example We want classic in the front and creative, colorfull at the back. The cards will be printed in relief, with very high quality of paper.
Insurance Broker
Colors
Designer to choose colors to be used in the design.

```html
<!DOCTYPE html>
<html lang="en">
<head>
<meta charset="utf-8">
<title>Tallow Partners – Business Card</title>
<link href="https://fonts.googleapis.com/css2?family=Lato:wght@400;700&display=swap" rel="stylesheet">
<style>
  :root {
    --backdrop: #3a3330;
    --card: #121212;
    --card-edge: #1c1c1c;
    --orange: #f26f21;
    --blue: #29a3e0;
    --text-grey: #9a9a9a;
    --rule: #2c2c2c;
    --silver: #d4d4d4;
  }
  * { margin: 0; padding: 0; box-sizing: border-box; }
  html, body { width: 1200px; height: 844px; overflow: hidden; }
  body {
    background: var(--backdrop);
    font-family: "Lato", Arial, sans-serif;
    display: flex;
    align-items: center;
    justify-content: center;
    gap: 60px;
  }
  .card {
    width: 520px;
    height: 300px;
    background: var(--card);
    border: 1px solid var(--card-edge);
    box-shadow: 0 14px 30px rgba(0,0,0,.45);
    position: relative;
  }
  /* Front: contact side */
  .card-front { display: flex; }
  .brand-panel {
    width: 230px;
    display: flex;
    flex-direction: column;
    align-items: center;
    justify-content: center;
    gap: 14px;
    border-right: 1px solid var(--rule);
  }
  .brand-dot {
    width: 70px; height: 70px;
    border-radius: 50%;
    border: 7px solid var(--orange);
  }
  .brand-name {
    color: var(--blue);
    font-weight: 700;
    font-size: 17px;
    letter-spacing: .5px;
  }
  .contact-panel {
    flex: 1;
    padding: 58px 24px 0 26px;
    color: var(--text-grey);
    font-size: 13px;
    line-height: 1.4;
  }
  .person-name {
    font-size: 19px;
    font-weight: 400;
    text-transform: uppercase;
    letter-spacing: .3px;
    line-height: 1.1;
  }
  .person-name .first { color: var(--orange); }
  .person-name .last { color: var(--blue); }
  .person-role { font-size: 13px; margin-bottom: 12px; }
  .contact-line { display: flex; align-items: center; gap: 6px; }
  .contact-line svg { width: 13px; height: 13px; flex: none; fill: var(--orange); }
  .address { margin-top: 14px; }
  /* Back: brand side */
  .card-back {
    display: flex;
    flex-direction: column;
    align-items: center;
    justify-content: center;
    gap: 20px;
  }
  .back-dot {
    width: 76px; height: 76px;
    border-radius: 50%;
    border: 6px solid var(--silver);
  }
  .back-name {
    color: var(--silver);
    font-weight: 700;
    font-size: 30px;
    text-transform: uppercase;
    letter-spacing: 1px;
  }
</style>
</head>
<body>
  <section class="card card-front">
    <div class="brand-panel">
      <div class="brand-dot"></div>
      <div class="brand-name">Tallow Partners</div>
    </div>
    <div class="contact-panel">
      <h1 class="person-name"><span class="first">Dorian</span> <span class="last">Whitlock</span></h1>
      <p class="person-role">Managing Director</p>
      <p class="contact-line">
        <svg viewBox="0 0 16 16" aria-hidden="true"><path d="M2 5c0-2 2-3 6-3s6 1 6 3v1h-3V5H5v1H2zM4 7h8l2 6H2z"/></svg>
        (+244) 947 582 316
      </p>
      <p class="contact-line">
        <svg viewBox="0 0 16 16" aria-hidden="true"><path d="M1 3h14v10H1zM2 4l6 5 6-5"/></svg>
        dorian.whitlock@tallow-p.example
      </p>
      <p class="address">N° 17/18 Rua Veloso - R / C<br>2B Direita<br>Bairro Mutamba - Luanda</p>
    </div>
  </section>

  <section class="card card-back">
    <div class="back-dot"></div>
    <div class="back-name">Tallow Partners</div>
  </section>
</body>
</html>
```